Branding Guide and Website for Q7Systems

Need an experienced Graphics Designer with a proven track record to create a design and branding guide for all media formats. From this guide you will then create a new website design for Q7systems.com.
There will be 8 pages (to start) with the new website. Each page will have multiple features and panels each need to have individual attention and customization that collectively fit together into a single cohesive look and feel.
We have not been able to get good designs I’m attaching one version which is the best we’ve received which is not bad but needs to be polished up better and the images need to change. I’d like to have some other accent colors but not too much I like the white, dark blue, gray, dark gray style.
Here are some sites that I like –
http://www.brelvant.com/
https://www.vontaric.com/ (layout good, graphics not great)
http://www.glastrek.com/ (good layout and graphics, too much animation)
https://www.pendrowix.com/ (a little boring but the colors and some of the top images are good)
https://www.tarnowelk.com/ (a little over the top colors are off but they have some good info graphics)
We don’t expect you will code the site however if you have that capability we’ll need it responsive/flat for mobile. Otherwise we can find someone to do the programming and we’ll just need the design files and images.
Branding guide will be used for web, email, print etc. so you’ll need to consider all guidelines for all formats. That is about it let me know if any questions we can have a call to discuss further if it is easier.
Not sure why they want a minimum of 300 words I’m done now but apparently have to keep typing so that is what I’m doing and Ok I’m at 300 words, almost there and we’re here now.

Target Market(s)

Customers looking for IT Services, Private Cloud, Security Services, Advanced Support, Fully Managed or Co-Managed IT.

Industry/Entity Type

It Company

Number of Pages Required

5+ page

Font styles to use
Sans Serif

Colors
0255a3
959595
e6e6e6
ffffff

Requirements
Must have
• Clean, professional and modern look using iconography, info graphics, flat etc.

```html
<!DOCTYPE html>
<html lang="en">
<head>
<meta charset="utf-8">
<title>Q7Systems — IT Service Excellence</title>
<link rel="stylesheet" href="https://fonts.googleapis.com/css2?family=Open+Sans:wght@400;600;700;800&display=swap">
<style>
:root{
  --blue:#0255a3;
  --blue-dark:#0a2c52;
  --navy:#061a33;
  --gray:#959595;
  --gray-dark:#555b62;
  --text:#33383d;
  --light:#e6e6e6;
  --soft:#f3f4f5;
  --white:#ffffff;
  --yellow:#f5b918;
  --footer:#232629;
  --footer-line:#34383c;
}
*{box-sizing:border-box;margin:0;padding:0}
html,body{width:1200px;height:2704px;overflow:hidden}
body{font-family:"Open Sans",Arial,sans-serif;color:var(--text);background:var(--white)}
.page{width:1200px;height:2704px;position:relative}

/* navigation */
.site-nav{height:56px;display:flex;align-items:center;justify-content:space-between;padding:0 60px;background:var(--white);border-bottom:1px solid var(--light)}
.brand{display:flex;align-items:center;gap:10px;font-weight:800;font-size:22px;color:var(--blue);letter-spacing:.3px}
.brand-mark{width:16px;height:16px;background:var(--blue)}
.nav-links{display:flex;gap:30px;list-style:none}
.nav-links li{font-size:11px;font-weight:600;color:var(--gray-dark);letter-spacing:.4px;text-transform:uppercase}
.nav-links li.active{color:var(--blue)}

/* hero */
.hero{position:relative;height:536px;background:linear-gradient(100deg,#06162b 0%,#0b2f57 45%,#0d4a86 75%,#0a3a6b 100%);overflow:hidden}
.hero-art{position:absolute;right:70px;top:50px;width:520px;height:430px;border-radius:50%;background:radial-gradient(circle at 50% 45%,rgba(120,200,255,.55) 0%,rgba(40,130,220,.35) 40%,rgba(10,60,120,0) 70%)}
.hero-copy{position:absolute;left:90px;top:180px;color:var(--white)}
.hero-copy h1{font-size:44px;font-weight:800;letter-spacing:.5px}
.hero-copy p{font-size:15px;margin-top:10px;color:#cfe0f3}
.btn-yellow{display:inline-block;margin-top:34px;padding:14px 28px;background:var(--yellow);color:var(--white);font-size:12px;font-weight:700;letter-spacing:.6px}
.hero-arrow{position:absolute;top:250px;width:30px;height:40px}
.hero-arrow.left{left:14px}.hero-arrow.right{right:14px}

/* section shared */
.section-title{text-align:center;font-size:26px;font-weight:800;color:var(--text);letter-spacing:.3px}
.section-title::after{content:"";display:block;width:44px;height:3px;background:var(--blue);margin:12px auto 0}
.section-lead{width:560px;margin:16px auto 0;text-align:center;font-size:12px;line-height:19px;color:var(--gray)}

/* what we do */
.what-we-do{height:488px;background:var(--soft);padding-top:46px}
.service-grid{width:960px;margin:44px auto 0;display:grid;grid-template-columns:repeat(3,1fr);column-gap:50px;row-gap:44px}
.service{display:flex;gap:16px}
.service svg{flex:none;width:44px;height:44px}
.service h3{font-size:16px;font-weight:700;color:var(--text);margin-bottom:6px}
.service p{font-size:11px;line-height:17px;color:var(--gray)}

/* help */
.help{height:520px;padding-top:48px}
.tile-row{width:1000px;margin:36px auto 0;display:grid;grid-template-columns:repeat(4,1fr);gap:20px}
.tile-image{height:150px}
.tile-image.network{background:linear-gradient(135deg,#0d3f77,#3f86c9)}
.tile-image.web{background:linear-gradient(135deg,#2b2f36,#9a2a3a)}
.tile-image.apps{background:linear-gradient(135deg,#5c6670,#c7ccd2)}
.tile-image.mind{background:linear-gradient(135deg,#4b5a6a,#a9b7c4)}
.tile h3{text-align:center;font-size:16px;font-weight:700;margin-top:14px}
.tile p{text-align:center;font-size:11px;line-height:16px;color:var(--gray);margin-top:6px;padding:0 12px}
.clients-note{text-align:center;font-size:11px;color:var(--gray);margin-top:28px}
.client-row{display:flex;justify-content:center;gap:64px;margin-top:22px}
.client-row span{font-size:22px;font-weight:600;color:var(--gray)}

/* testimonials */
.testimonials{height:380px;background:var(--soft);padding-top:60px}
.quote-row{width:1000px;margin:46px auto 0;display:grid;grid-template-columns:repeat(3,1fr);gap:40px}
.quote{text-align:center;font-size:12px;line-height:19px;font-style:italic;color:var(--gray)}
.quote cite{display:block;margin-top:14px;font-style:normal;font-weight:600;color:var(--blue)}

/* different */
.different{position:relative;height:380px;padding-top:54px;overflow:hidden}
.different-art{position:absolute;right:0;top:10px;width:330px;height:360px;background:radial-gradient(circle at 60% 50%,#dfe6ee 0%,#f2f4f7 55%,rgba(255,255,255,0) 75%)}
.different .section-lead{width:600px}
.btn-blue{display:block;width:140px;margin:28px auto 0;padding:13px 0;background:var(--blue);color:var(--white);text-align:center;font-size:11px;font-weight:700;letter-spacing:.6px}

/* footer */
.site-footer{height:344px;background:var(--footer);color:#9aa0a6;padding:48px 90px 0;display:grid;grid-template-columns:1.1fr 1fr 1fr 1fr;gap:40px;position:relative}
.social{display:flex;gap:8px}
.social span{width:26px;height:26px;border-radius:50%;border:2px solid #8c9298}
.legal{font-size:11px;line-height:18px;margin-top:18px}
.site-footer h4{font-size:15px;color:var(--white);font-weight:600;padding-bottom:10px;border-bottom:1px solid var(--footer-line);margin-bottom:14px}
.contact p{font-size:11px;line-height:19px}
.field{height:28px;background:var(--white);margin-bottom:10px;font-size:10px;color:var(--gray);padding:7px 10px}
.btn-submit{display:inline-block;background:var(--blue);color:var(--white);font-size:10px;font-weight:700;padding:8px 16px;letter-spacing:.5px}
.browse ul{list-style:none}
.browse li{font-size:11px;line-height:22px}
.browse li::before{content:"";display:inline-block;width:6px;height:6px;background:var(--blue);margin-right:8px;vertical-align:middle}
.to-top{position:absolute;right:20px;bottom:18px;font-size:11px;color:#8c9298}
</style>
</head>
<body>
<div class="page">

<header class="site-nav">
  <div class="brand"><span class="brand-mark"></span>Q7Systems</div>
  <ul class="nav-links">
    <li class="active">Home</li><li>Managed Services</li><li>Corporate Cloud</li><li>Cloud Solutions</li><li>Network Operations</li><li>Services</li><li>Company</li>
  </ul>
</header>

<section class="hero">
  <div class="hero-art" role="img" aria-label="Glowing cloud with a key over a dark digital background"></div>
  <svg class="hero-arrow left" viewBox="0 0 30 40"><path d="M20 6 L8 20 L20 34" fill="none" stroke="#ffffff" stroke-width="3"/></svg>
  <svg class="hero-arrow right" viewBox="0 0 30 40"><path d="M10 6 L22 20 L10 34" fill="none" stroke="#ffffff" stroke-width="3"/></svg>
  <div class="hero-copy">
    <h1>IT SERVICE EXCELLENCE</h1>
    <p>Driving for Continuous Services improvement for our Clients</p>
    <span class="btn-yellow">GET STARTED NOW</span>
  </div>
</section>

<section class="what-we-do">
  <h2 class="section-title">WHAT WE DO</h2>
  <p class="section-lead">Providing IT services since 2005, we help businesses run smoothly, stay secure and grow with dependable technology.</p>
  <div class="service-grid">
    <div class="service">
      <svg viewBox="0 0 44 44"><circle cx="22" cy="22" r="9" fill="none" stroke="#0255a3" stroke-width="3"/><path d="M22 4v7M22 33v7M4 22h7M33 22h7M9 9l5 5M30 30l5 5M9 35l5-5M30 14l5-5" stroke="#0255a3" stroke-width="3"/></svg>
      <div><h3>Managed Services</h3><p>We provide comprehensive technology management, IT services and support so your team can focus on work.</p></div>
    </div>
    <div class="service">
      <svg viewBox="0 0 44 44"><path d="M12 32h22a7 7 0 0 0 0-14 10 10 0 0 0-19-2 8 8 0 0 0-3 16z" fill="none" stroke="#0255a3" stroke-width="3"/></svg>
      <div><h3>Private Cloud</h3><p>We let systems and applications run on cloud capacity that is dedicated, protected and scalable.</p></div>
    </div>
    <div class="service">
      <svg viewBox="0 0 44 44"><path d="M22 4l14 6v10c0 10-6 16-14 20C14 36 8 30 8 20V10z" fill="none" stroke="#0255a3" stroke-width="3"/><path d="M15 22l5 5 9-10" fill="none" stroke="#0255a3" stroke-width="3"/></svg>
      <div><h3>Security Services</h3><p>Our security team monitors, detects and responds to threats around the clock for full protection.</p></div>
    </div>
    <div class="service">
      <svg viewBox="0 0 44 44"><path d="M8 26v-4a14 14 0 0 1 28 0v4" fill="none" stroke="#0255a3" stroke-width="3"/><rect x="5" y="24" width="7" height="12" fill="#0255a3"/><rect x="32" y="24" width="7" height="12" fill="#0255a3"/></svg>
      <div><h3>Advanced Support</h3><p>Skilled engineers are ready to solve problems fast with remote and onsite help whenever you need.</p></div>
    </div>
    <div class="service">
      <svg viewBox="0 0 44 44"><circle cx="22" cy="8" r="5" fill="#0255a3"/><circle cx="8" cy="36" r="5" fill="#0255a3"/><circle cx="36" cy="36" r="5" fill="#0255a3"/><path d="M22 13v10M22 23L8 31M22 23l14 8" stroke="#0255a3" stroke-width="3"/></svg>
      <div><h3>Network Services</h3><p>We design, build and maintain networks that stay fast, stable and ready for future growth.</p></div>
    </div>
    <div class="service">
      <svg viewBox="0 0 44 44"><path d="M36 16A15 15 0 0 0 8 18M8 28a15 15 0 0 0 28-2" fill="none" stroke="#0255a3" stroke-width="3"/><path d="M36 6v10H26M8 38V28h10" fill="none" stroke="#0255a3" stroke-width="3"/></svg>
      <div><h3>Disaster Recovery</h3><p>Backup and recovery plans keep your data safe and your business running after any incident.</p></div>
    </div>
  </div>
</section>

<section class="help">
  <h2 class="section-title">HOW CAN WE HELP YOUR BUSINESS?</h2>
  <p class="section-lead">Our complete managed service approach gives you a single partner for technology, support and security, delivered by a team that knows your business.</p>
  <div class="tile-row">
    <div class="tile"><div class="tile-image network" role="img" aria-label="Glowing network connections photo"></div><h3>Your Network</h3><p>A reliable, scalable network built around the way your people work.</p></div>
    <div class="tile"><div class="tile-image web" role="img" aria-label="Padlock on a digital screen photo"></div><h3>Your Web Presence</h3><p>A secure, fast web presence that keeps customers coming back.</p></div>
    <div class="tile"><div class="tile-image apps" role="img" aria-label="Hands typing on a laptop photo"></div><h3>Your Applications</h3><p>Business applications managed and updated in the cloud with care.</p></div>
    <div class="tile"><div class="tile-image mind" role="img" aria-label="Engineer working in a server room photo"></div><h3>Your Piece of Mind</h3><p>Round the clock monitoring so you can focus on growth.</p></div>
  </div>
  <p class="clients-note">Trusted by growing companies across many industries, from startups to established enterprise teams.</p>
  <div class="client-row">
    <span>Sonvera</span><span>Maltrix</span><span>Pixlane</span><span>Framebank</span><span>Tallybox</span>
  </div>
</section>

<section class="testimonials">
  <h2 class="section-title">WHAT ARE PEOPLE SAYING ABOUT Q7SYSTEMS</h2>
  <div class="quote-row">
    <p class="quote">"Their team took over our entire IT setup and the difference was clear within weeks. Systems are faster, issues are rare and support always answers."<cite>Dana Holt, Riverton</cite></p>
    <p class="quote">"Moving to their private cloud was smooth and well planned. We now have better uptime, clearer costs and a partner we truly trust."<cite>Priya Nand, Lakeford</cite></p>
    <p class="quote">"Security used to keep me awake at night. With constant monitoring and fast response, we finally feel protected and in control."<cite>Evan Cole, Westbrook</cite></p>
  </div>
</section>

<section class="different">
  <div class="different-art" role="img" aria-label="Illustration of a technician surrounded by connected network devices"></div>
  <h2 class="section-title">WE ARE DIFFERENT</h2>
  <p class="section-lead">We treat your business as our own. Our engineers learn how you work, plan ahead for growth and fix problems before they reach your desk. Clear pricing, honest advice and a single point of contact make technology simple again for every team we serve.</p>
  <span class="btn-blue">HOW IT WORKS</span>
</section>

<footer class="site-footer">
  <div>
    <div class="social"><span></span><span></span><span></span></div>
    <p class="legal">© 2024 Q7Systems<br>All Rights Reserved<br>Privacy Policy</p>
  </div>
  <div class="contact">
    <h4>Contact us</h4>
    <p>1417 Harbor Crest Dr, Suite 210<br>Fairview, CA 90458<br>(555) 014-2280<br>info@q7systems.com</p>
  </div>
  <div class="newsletter">
    <h4>Newsletter</h4>
    <div class="field">Name</div>
    <div class="field">Email address</div>
    <span class="btn-submit">SUBMIT</span>
  </div>
  <div class="browse">
    <h4>Browse</h4>
    <ul><li>Managed Services</li><li>Private Cloud</li><li>Security Services</li><li>Network Operations</li><li>Company</li></ul>
  </div>
  <span class="to-top">Top</span>
</footer>

</div>
</body>
</html>
```